Art Business Needs a Wordpress Theme

I need a Wordpress theme for my company, Pim Pim Nook. Pim Pim stands for Love, Local and the company's focus is to increase awareness of local art and artists. The site will have a blog with posts that showcase local art, art how-to techniques, featured artists and art events. These could be broken down into separate pages or just kept within the homepage. I have a logo that I would like to incorporate. The only request I will make about the layout is that it can feature pictures prominently. Eventually with the help of a Fundmoor campaign I would like to turn the site into an upscale e-commerce platform for member artists of the site. The blog that you are designing will be built on as the business grows into its full vision.

Target Market(s)

Young professionals, Art fans and home designers

Industry/Entity Type

Business

Number of Pages Required

3 page

Font styles to use
Sans Serif

Colors
eda3c7
e667a6
e34197
f59195
f04a50
f68d4d
f37122

Requirements
Must have
• An about page and a contact page. I would like it if the logo was featured on the top left of the screen along with the words Love. Local. Art.
Nice to have
• Perhaps if possible it would be cool to have a way for people to enter their email if they were interested in joining a mailing list or having the Social media information displayed on a sidebar.

```html
<!DOCTYPE html>
<html lang="en">
<head>
<meta charset="utf-8">
<title>Pim Pim Nook — Love. Local. Art.</title>
<link href="https://fonts.googleapis.com/css2?family=Open+Sans:wght@400;600;700;800&display=swap" rel="stylesheet">
<style>
:root{
  --pink-soft:#f7d3e3;
  --pink-bg:#f4c4da;
  --pink-nav:#e96fa8;
  --pink-main:#e34197;
  --pink-mid:#e667a6;
  --pink-light:#eda3c7;
  --coral:#f04a50;
  --orange:#f37122;
  --text:#555;
  --muted:#999;
  --white:#fff;
  --line:#e6e6e6;
}
*{box-sizing:border-box;margin:0;padding:0}
html,body{width:1200px;height:2344px;overflow:hidden}
body{font-family:"Open Sans",Arial,sans-serif;color:var(--text);background:var(--pink-bg);position:relative;font-size:13px}
.abs{position:absolute}
.topnav{left:0;top:0;width:1200px;height:40px;background:var(--pink-nav);display:flex;justify-content:center;gap:58px;align-items:center}
.topnav a{color:#fff;text-decoration:none;font-size:14px}
.header{left:0;top:40px;width:1200px;height:200px;background:linear-gradient(#fbe6ef,var(--pink-soft))}
.header .hills{position:absolute;left:0;bottom:0;width:1200px;height:110px}
.brand{left:500px;top:54px;width:200px;text-align:center}
.brand .mark{width:110px;height:110px;border-radius:50%;background:var(--white);border:4px solid var(--pink-light);margin:0 auto 8px}
.brand .name{color:var(--pink-main);font-weight:700;font-size:15px}
.brand .tag{color:var(--pink-mid);font-size:11px;margin-top:2px}
.slider{left:100px;top:256px;width:1000px;height:456px;background:linear-gradient(90deg,#e9f0ee,#f3dfe8 55%,#ede0f2);border:6px solid var(--white);box-shadow:0 2px 6px rgba(0,0,0,.12)}
.slide-photo{position:absolute;left:24px;top:18px;width:430px;height:410px;background:var(--white);padding:10px;transform:rotate(-2deg);box-shadow:0 2px 8px rgba(0,0,0,.2)}
.slide-photo div{width:100%;height:100%;background:linear-gradient(135deg,#c9b7a8,#e7d6cf 45%,#b6a6c8)}
.slide-text{position:absolute;left:560px;top:140px;width:400px}
.slide-text h1{font-size:40px;font-weight:800;color:#3a3a3a;letter-spacing:1px}
.slide-text p{font-size:13px;line-height:20px;color:#777;margin:12px 0 20px}
.btn{display:inline-block;background:var(--pink-main);color:#fff;font-size:12px;font-weight:700;padding:9px 18px;border-radius:3px}
.arrows{position:absolute;right:14px;bottom:14px;display:flex;gap:6px}
.main{left:100px;top:760px;width:736px;height:1360px;background:var(--white);padding:32px 24px}
.section-title{color:var(--pink-main);font-size:20px;font-weight:600;text-transform:uppercase;border-bottom:1px solid var(--line);padding-bottom:10px}
.events{display:flex;gap:24px;margin-top:20px}
.event{width:213px}
.event .ph{height:180px}
.event h3{font-size:14px;font-weight:600;color:#444;margin:14px 0 6px}
.meta{font-size:11px;color:var(--muted);margin-bottom:8px}
.meta span{margin-right:18px}
.event p,.artist p{font-size:12px;line-height:18px;color:#888}
.artists{margin-top:22px}
.artist{display:flex;gap:24px;margin-bottom:22px;height:232px}
.artist .ph{width:320px;height:232px;flex:none}
.artist h3{font-size:15px;line-height:21px;font-weight:700;color:#444;margin-bottom:8px}
.artist .more{font-size:11px;font-weight:700;color:#444;margin-top:10px}
.pager{display:flex;gap:6px;justify-content:center;margin-top:8px}
.pager span{border:1px solid var(--line);font-size:11px;padding:4px 9px;color:#777}
.pager .on{background:var(--pink-main);color:#fff;border-color:var(--pink-main)}
.side{left:856px;top:760px;width:244px}
.widget{background:var(--white);margin-bottom:16px}
.socials{display:flex;justify-content:space-around;padding:16px 10px 10px}
.socials div{text-align:center;font-size:9px;color:#888}
.socials i{display:block;width:34px;height:34px;border-radius:4px;margin:0 auto 4px}
.search{display:flex;padding:0 12px 16px}
.search span{flex:1;border:1px solid var(--line);font-size:11px;color:#aaa;padding:6px}
.search b{width:30px;background:var(--coral)}
.news{border:3px solid var(--pink-light);padding:20px 18px;text-align:center}
.news h4{color:var(--pink-main);font-size:12px;font-weight:600;line-height:17px;margin-bottom:14px}
.news .field{border:1px solid var(--line);font-size:11px;color:#aaa;text-align:left;padding:7px;margin-bottom:10px}
.ad{height:232px;background:linear-gradient(#d9eef7,#7ec3e4);padding:18px;position:relative}
.ad .help{font-size:18px;font-weight:800;color:#1f6fae;line-height:23px;width:122px}
.ad .band{position:absolute;left:0;bottom:22px;width:100%;background:#fff;color:#1f6fae;font-weight:800;font-size:20px;text-align:center;padding:7px 0}
.ad .kid{position:absolute;right:14px;top:26px;width:90px;height:120px;background:linear-gradient(#e8b48f,#c48860)}
.wtitle{background:var(--pink-mid);color:#fff;font-size:13px;font-weight:600;padding:9px 12px}
.tweet{display:flex;gap:10px;padding:12px;border-bottom:1px solid var(--line);font-size:11px;line-height:15px}
.avatar{width:34px;height:34px;border-radius:50%;background:var(--pink-light);flex:none}
.tweet b{color:var(--pink-main)}
.fans{display:grid;grid-template-columns:repeat(5,1fr);gap:6px;padding:8px 12px}
.fans i{height:38px;background:#d8c8d0}
.footer{left:0;top:2180px;width:1200px;height:164px;background:var(--pink-nav);text-align:center;color:#fff}
.ficons{display:flex;justify-content:center;gap:14px;padding-top:28px}
.ficons i{width:30px;height:30px;background:#fff;border-radius:4px;opacity:.9}
.flinks{font-size:12px;margin-top:18px;word-spacing:6px}
.copy{font-size:11px;margin-top:8px;opacity:.9}
</style>
</head>
<body>
<nav class="topnav abs"><a>Home</a><a>About Us</a><a>Featured Articles</a><a>Galleries</a><a>Info</a><a>Sign In</a><a>Contact Us</a></nav>

<header class="header abs">
  <svg class="hills" viewBox="0 0 1200 110" role="img" aria-label="soft hills and trees decoration">
    <path d="M0 80 Q300 40 600 75 T1200 70 V110 H0Z" fill="#f0bcd4"/>
    <path d="M0 95 Q400 65 800 92 T1200 88 V110 H0Z" fill="#eaaecb"/>
  </svg>
</header>
<div class="brand abs"><div class="mark"></div><div class="name">Pim Pim Nook</div><div class="tag">Love. Local. Art.</div></div>

<section class="slider abs">
  <div class="slide-photo"><div role="img" aria-label="photo of an artist holding a paint palette"></div></div>
  <div class="slide-text">
    <h1>ART AND ARTISTS</h1>
    <p>Lorem ipsum dolor sit amet, consectetur adipiscing elit, sed do eiusmod tempor incididunt ut labore et dolore magna aliqua. Ut enim ad minim veniam.</p>
    <span class="btn">READ MORE</span>
  </div>
  <div class="arrows"><svg width="20" height="20"><path d="M13 4 7 10l6 6" stroke="#fff" stroke-width="3" fill="none"/></svg><svg width="20" height="20"><path d="m7 4 6 6-6 6" stroke="#fff" stroke-width="3" fill="none"/></svg></div>
</section>

<main class="main abs">
  <h2 class="section-title">Art Events</h2>
  <div class="events">
    <article class="event"><div class="ph" role="img" aria-label="photo of a gallery interior" style="background:linear-gradient(#c9a48d,#7b4b3c)"></div><h3>Duis aute irure dolor in</h3><div class="meta">March 25, 2015</div><p>Lorem ipsum dolor sit amet, consectetur adipiscing elit, sed do eiusmod tempor incididunt ut labore.</p></article>
    <article class="event"><div class="ph" role="img" aria-label="photo of visitors viewing artwork" style="background:linear-gradient(#e6e2dc,#a9a39a)"></div><h3>Duis aute irure dolor in</h3><div class="meta">March 25, 2015</div><p>Lorem ipsum dolor sit amet, consectetur adipiscing elit, sed do eiusmod tempor incididunt ut labore.</p></article>
    <article class="event"><div class="ph" role="img" aria-label="photo of an art exhibition room" style="background:linear-gradient(#ece7e0,#b9aea3)"></div><h3>Duis aute irure dolor in</h3><div class="meta">March 25, 2015</div><p>Lorem ipsum dolor sit amet, consectetur adipiscing elit, sed do eiusmod tempor incididunt ut labore.</p></article>
  </div>

  <h2 class="section-title" style="margin-top:56px">Featured Artists</h2>
  <div class="artists">
    <article class="artist"><div class="ph" role="img" aria-label="colourful abstract painting" style="background:linear-gradient(135deg,#f2c24a,#e35b6a,#4aa3d8)"></div><div><h3>Nemo enim ipsam voluptatem quia voluptas sit aspernatur aut odit aut fugit.</h3><div class="meta"><span>March 25, 2015</span><span>2 Comments</span><span>By David</span></div><p>Lorem ipsum dolor sit amet, consectetur adipiscing elit, sed do eiusmod tempor incididunt ut labore et dolore magna aliqua. Ut enim ad minim veniam, quis nostrud exercitation ullamco laboris nisi ut aliquip ex ea commodo consequat.</p><div class="more">LEARN MORE »</div></div></article>
    <article class="artist"><div class="ph" role="img" aria-label="child's painting of a house" style="background:linear-gradient(#8fc6e8,#f4e6b0 60%,#6fb36a)"></div><div><h3>Nemo enim ipsam voluptatem quia voluptas sit aspernatur aut odit aut fugit.</h3><div class="meta"><span>March 25, 2015</span><span>2 Comments</span><span>By David</span></div><p>Lorem ipsum dolor sit amet, consectetur adipiscing elit, sed do eiusmod tempor incididunt ut labore et dolore magna aliqua. Ut enim ad minim veniam, quis nostrud exercitation ullamco laboris nisi ut aliquip ex ea commodo consequat.</p><div class="more">LEARN MORE »</div></div></article>
    <article class="artist"><div class="ph" role="img" aria-label="painting of boats on water" style="background:linear-gradient(#3f7fc0,#e36a4a 55%,#2c5d9a)"></div><div><h3>Nemo enim ipsam voluptatem quia voluptas sit aspernatur aut odit aut fugit.</h3><div class="meta"><span>March 25, 2015</span><span>2 Comments</span><span>By David</span></div><p>Lorem ipsum dolor sit amet, consectetur adipiscing elit, sed do eiusmod tempor incididunt ut labore et dolore magna aliqua. Ut enim ad minim veniam, quis nostrud exercitation ullamco laboris nisi ut aliquip ex ea commodo consequat.</p><div class="more">LEARN MORE »</div></div></article>
  </div>
  <div class="pager"><span>Prev</span><span class="on">1</span><span>2</span><span>3</span><span>4</span><span>5</span><span>6</span><span>...</span><span>20</span><span>Next</span></div>
</main>

<aside class="side abs">
  <div class="widget">
    <div class="socials">
      <div><i style="background:var(--orange)"></i>RSS</div>
      <div><i style="background:var(--coral)"></i>Subscribe</div>
      <div><i style="background:#5aaee0"></i>Chirper</div>
      <div><i style="background:#3b5a9a"></i>Facepage</div>
    </div>
    <div class="search"><span>Search</span><b></b></div>
  </div>
  <div class="widget news">
    <h4>Get my latest updates sent to your inbox</h4>
    <div class="field">Your Name</div>
    <div class="field">Email Address</div>
    <span class="btn" style="background:var(--pink-mid)">Sign Me Up</span>
  </div>
  <div class="widget ad">
    <div class="help">Paint, play and grow with us</div>
    <div class="kid" role="img" aria-label="photo of a smiling child"></div>
    <div class="band">SUNNY STEPS FAIR</div>
  </div>
  <div class="widget">
    <div class="wtitle">Chirper Updates</div>
    <div class="tweet"><div class="avatar"></div><div><b>Pim Pim Nook</b><br>New local gallery opening this week, come and say hello.</div></div>
    <div class="tweet"><div class="avatar"></div><div><b>Pim Pim Nook</b><br>Meet our featured artist of the month on the blog today.</div></div>
    <div class="tweet"><div class="avatar"></div><div><b>Pim Pim Nook</b><br>Five simple watercolour tips for total beginners.</div></div>
  </div>
  <div class="widget">
    <div class="wtitle">Follow Us on Facepage</div>
    <div class="tweet" style="border:0"><div class="avatar" style="border-radius:4px"></div><div><b>Pim Pim Nook</b><br>22,999 people like this</div></div>
    <div class="fans"><i></i><i></i><i></i><i></i><i></i><i></i><i></i><i></i><i></i><i></i></div>
    <div style="font-size:11px;padding:6px 12px 14px;color:#888">Facepage social plugin</div>
  </div>
</aside>

<footer class="footer abs">
  <div class="ficons"><i></i><i></i><i></i><i></i><i></i></div>
  <div class="flinks">Home | Contact | Topics | Featured Artists | Discussions | Helpful Links</div>
  <div class="copy">Copyright © 2014 - 2015 Pim Pim Nook. All Rights Reserved.</div>
</footer>
</body>
</html>
```